BRIVAN 2026 Flyer for Conference

BRIVAN needs a design for a 1-page flyer that we will hand out at an upcoming event & then later post online as a pdf. There are 3 elements which need to be on the flyer:

1) A logo. This should be prominent on the design (e.g., in the middle). The flyer should use the colors that are in that logo (e.g., for accents, design elements, and/or text; not all of these have to be used):
Dark blue: #185577
Med blue: #327C9A
Teal: #4EB1C2
Light Teal: #9EDBE6

2) The conference theme -- Oceans of Knowledge: Diving into Information Literacy -- should be at the flyer's top.

3) Finally, these six tracks should be listed below the theme and the logo (it's font size should be at least a couple sizes smaller than the size used for the theme):
- Pearls of Pedagogy: Teaching Techniques that Work
- The Depth Gauge: Measuring Instructional Impact
- Techtonic Shifts: Innovation and Educational Technology
- Captain's Log: Navigating Leadership in Library Instruction
- Swimming Together: Collaborating with Others
- The Bermuda Triangle: Exploring (Seemingly) Eternal Challenges

Font styles to use
Sans Serif

Colors
0094D4
00A9DD
6FCCEA
C7EBF8
E9F6FB

Requirements
Must have
• The 3 elements listed in the description: 1) the logo, 2) the text of the theme and 3) the text for the tracks.

```html
<!DOCTYPE html>
<html lang="en">
<head>
<meta charset="utf-8">
<title>BRIVAN 2026 – Oceans of Knowledge</title>
<link rel="stylesheet" href="https://fonts.googleapis.com/css2?family=Nunito+Sans:wght@400;600;700;800&display=swap">
<style>
  :root {
    --stage: #9a9a9a;
    --deep: #0b2a33;
    --ocean: #0f5663;
    --teal: #4eb1c2;
    --light-teal: #9edbe6;
    --dark-blue: #185577;
    --rock: #4a3b2e;
    --white: #ffffff;
  }
  * { box-sizing: border-box; margin: 0; padding: 0; }
  html, body {
    width: 1199px; height: 1200px; overflow: hidden;
    background: var(--stage);
    font-family: "Nunito Sans", sans-serif;
  }
  .flyer {
    position: absolute; left: 229px; top: 75px;
    width: 742px; height: 1050px; overflow: hidden;
    color: var(--white);
    box-shadow: 6px 8px 14px rgba(0,0,0,.35);
  }
  .flyer__photo {
    position: absolute; inset: 0;
    background:
      radial-gradient(ellipse 50% 32% at 72% 14%, #6b5540 0%, var(--rock) 55%, transparent 100%),
      radial-gradient(ellipse 30% 20% at 48% 38%, #cfe7ea 0%, rgba(120,190,200,.5) 45%, transparent 100%),
      radial-gradient(ellipse 60% 50% at 85% 60%, #1a8a96 0%, transparent 70%),
      linear-gradient(180deg, #203a3c 0%, var(--ocean) 45%, #0e4b56 75%, var(--deep) 100%);
  }
  .brand {
    position: absolute; top: 110px; left: 0; right: 0;
    text-align: center;
  }
  .brand__name {
    display: inline-flex; align-items: center; gap: 14px;
    font-weight: 800; font-size: 70px; letter-spacing: 2px;
    color: var(--light-teal); line-height: 1;
  }
  .brand__dot {
    width: 24px; height: 24px; border-radius: 50%;
    background: var(--light-teal);
  }
  .brand__place {
    margin-top: 14px;
    font-weight: 800; font-size: 18px; letter-spacing: 3px;
    color: var(--light-teal);
  }
  .theme {
    position: absolute; top: 518px; left: 0; right: 0;
    text-align: center;
    text-shadow: 3px 4px 6px rgba(0,0,0,.55);
  }
  .theme__title {
    font-weight: 600; font-size: 84px; line-height: 0.9;
    letter-spacing: 2px; text-transform: uppercase;
  }
  .theme__subtitle {
    margin-top: 8px;
    font-weight: 600; font-size: 30px; line-height: 1.2;
    letter-spacing: 0.5px; text-transform: uppercase;
  }
  .divider {
    position: absolute; top: 743px; left: 50%;
    transform: translateX(-50%);
  }
  .tracks {
    position: absolute; top: 787px; left: 0; right: 0;
    list-style: none; text-align: center;
    font-size: 18.5px; line-height: 30px;
  }
  .tracks__name { font-weight: 700; }
</style>
</head>
<body>
  <main class="flyer">
    <div class="flyer__photo" role="img" aria-label="Aerial photograph of turquoise ocean waves breaking white against a dark rocky coastline"></div>

    <header class="brand">
      <div class="brand__name"><span class="brand__dot"></span>BRIVAN 2026</div>
      <div class="brand__place">NORFOLK, VA · MAY 7-9</div>
    </header>

    <section class="theme">
      <h1 class="theme__title">Oceans of<br>Knowledge:</h1>
      <p class="theme__subtitle">Diving into Information Literacy</p>
    </section>

    <svg class="divider" width="270" height="16" viewBox="0 0 270 16" aria-hidden="true">
      <line x1="0" y1="8" x2="115" y2="8" stroke="#ffffff" stroke-width="2"/>
      <rect x="130" y="3" width="10" height="10" transform="rotate(45 135 8)" fill="none" stroke="#ffffff" stroke-width="2"/>
      <line x1="155" y1="8" x2="270" y2="8" stroke="#ffffff" stroke-width="2"/>
    </svg>

    <ul class="tracks">
      <li><span class="tracks__name">Pearls of Pedagogy:</span> Teaching Techniques that Work</li>
      <li><span class="tracks__name">The Depth Gauge:</span> Measuring Instructional Impact</li>
      <li><span class="tracks__name">Techtonic Shifts:</span> Innovation and Educational Technology</li>
      <li><span class="tracks__name">Captain's Log:</span> Navigating Leadership in Library Instruction</li>
      <li><span class="tracks__name">Swimming Together:</span> Collaborating with Others</li>
      <li><span class="tracks__name">The Bermuda Triangle:</span> Exploring (Seemingly) Eternal Challenges</li>
    </ul>
  </main>
</body>
</html>
```